Web Design For Manufacturing And Outsourcing Company

Pick up the pieces from our previous developer and help us complete our website.

5 pages - Home,Machining,Sourcing,About Us, and Contact

Attached you will find screen shots of previous direction but we're open to new ideas.

We can provide all text and images needed.

Thanks!

Number of Pages Required

5+ page

```html
<!DOCTYPE html>
<html lang="en">
<head>
<meta charset="utf-8">
<title>Corran Industries</title>
<link rel="stylesheet" href="https://fonts.googleapis.com/css2?family=Oswald:wght@500&family=Open+Sans:wght@400;600&family=Poppins:wght@400;500&display=swap">
<style>
  :root {
    --orange: #e8501c;
    --orange-deep: #d9461a;
    --ink: #1b1b1b;
    --header: #222222;
    --dark-panel: #1d1e21;
    --footer: #0c0c0c;
    --paper: #ffffff;
    --mist: #ececec;
    --text-grey: #555555;
    --line-grey: #cfcfcf;
  }
  * { box-sizing: border-box; margin: 0; padding: 0; }
  html, body { width: 1200px; height: 2270px; overflow: hidden; }
  body { position: relative; background: var(--paper); font-family: "Open Sans", Arial, sans-serif; color: var(--ink); }

  .site-header { position: absolute; left: 0; top: 0; width: 1200px; height: 83px; background: var(--header); z-index: 3; }
  .brand { position: absolute; left: 94px; top: 28px; display: flex; align-items: center; gap: 10px; color: var(--paper); font-family: "Open Sans", Arial, sans-serif; font-weight: 600; font-size: 19px; letter-spacing: 3px; }
  .brand-square { width: 20px; height: 26px; background: var(--orange); }
  .main-nav { position: absolute; top: 28px; left: 0; width: 1200px; font-size: 18px; }
  .main-nav a { position: absolute; color: var(--paper); text-decoration: none; white-space: nowrap; }
  .main-nav a.is-current { color: var(--orange); }

  .hero { position: absolute; left: 0; top: 83px; width: 1200px; height: 600px; background: radial-gradient(ellipse at 82% 45%, #e67a3a 0%, #7a4b3a 12%, #1f5e9c 30%, #0f3766 60%, #071a33 100%); }
  .hero-cut { position: absolute; left: 0; top: 590px; width: 1200px; height: 100px; }
  .hero-title { position: absolute; left: 88px; top: 225px; font-family: "Oswald", Arial, sans-serif; font-weight: 500; font-size: 92px; line-height: 1; color: var(--paper); }
  .hero-lead { position: absolute; left: 88px; top: 348px; font-size: 35px; line-height: 48px; color: var(--paper); }
  .hero-arrows { position: absolute; left: 88px; top: 455px; display: flex; gap: 10px; }
  .hero-arrows svg { width: 28px; height: 28px; }

  .about-frame { position: absolute; left: 98px; top: 713px; width: 324px; height: 408px; border: 3px solid var(--orange); }
  .about-card { position: absolute; left: 120px; top: 734px; width: 985px; height: 367px; background: var(--paper); border: 1px solid var(--line-grey); box-shadow: 0 4px 14px rgba(0,0,0,.18); }
  .about-photo { position: absolute; left: 0; top: 0; width: 370px; height: 367px; background: linear-gradient(135deg, #4a4a4a 0%, #9a9a9a 45%, #d8d8d8 75%, #6d6d6d 100%); }
  .about-body { position: absolute; left: 411px; top: 36px; width: 530px; }
  .about-title { font-family: "Poppins", Arial, sans-serif; font-weight: 500; font-size: 48px; line-height: 1.1; color: var(--ink); }
  .about-text { margin-top: 14px; font-size: 15.5px; line-height: 29px; color: var(--text-grey); text-align: justify; }
  .pill-button { display: inline-block; background: var(--orange); color: var(--paper); border-radius: 18px; font-family: "Poppins", Arial, sans-serif; font-size: 17px; text-align: center; line-height: 36px; }
  .about-body .pill-button { margin-top: 22px; width: 124px; }

  .services { position: absolute; left: 0; top: 1185px; width: 1200px; height: 600px; }
  .services-bg { position: absolute; left: 0; top: 0; width: 1200px; height: 600px; }
  .service { position: absolute; top: 150px; width: 460px; color: var(--paper); }
  .service-machining { left: 90px; }
  .service-sourcing { left: 659px; top: 154px; }
  .service-head { display: flex; align-items: center; gap: 24px; height: 48px; }
  .service-title { font-family: "Poppins", Arial, sans-serif; font-weight: 500; font-size: 33px; }
  .service-icons { width: 180px; height: 46px; background: linear-gradient(90deg, rgba(255,255,255,.85), rgba(255,255,255,.55)); border-radius: 4px; }
  .service-sourcing .service-icons { width: 175px; background: linear-gradient(90deg, rgba(255,255,255,.85), rgba(232,80,28,.9)); }
  .service-text { margin-top: 18px; font-size: 15px; line-height: 26.5px; text-align: justify; }
  .service-list { list-style: none; margin-top: 38px; }
  .service-sourcing .service-list { margin-top: 30px; }
  .service-list li { display: flex; align-items: center; gap: 8px; font-size: 20px; height: 38px; }
  .service-list svg { width: 18px; height: 18px; flex: none; }

  .contact { position: absolute; left: 0; top: 1783px; width: 1200px; height: 384px; background: linear-gradient(135deg, #f3f3f3 0%, #e4e4e4 40%, #f0f0f0 70%, #e2e2e2 100%); text-align: center; }
  .contact-title { position: absolute; top: 110px; width: 100%; font-family: "Poppins", Arial, sans-serif; font-weight: 400; font-size: 43px; color: var(--ink); }
  .contact-lead { position: absolute; top: 180px; width: 100%; font-family: "Poppins", Arial, sans-serif; font-weight: 500; font-size: 27px; color: var(--ink); }
  .contact .pill-button { position: absolute; left: 517px; top: 249px; width: 165px; font-size: 19px; }

  .site-footer { position: absolute; left: 0; top: 2167px; width: 1200px; height: 103px; background: var(--footer); color: #bdbdbd; font-size: 16px; text-align: center; line-height: 103px; }
</style>
</head>
<body>
  <header class="site-header">
    <div class="brand"><span class="brand-square"></span>CORRAN INDUSTRIES</div>
    <nav class="main-nav">
      <a class="is-current" style="left:575px">Home</a>
      <a style="left:675px">Machinging capabilies</a>
      <a style="left:904px">Sourcing</a>
      <a style="left:1026px">Contact us</a>
    </nav>
  </header>

  <section class="hero" role="img" aria-label="Close-up of a lathe cutting metal with sparks flying">
  </section>
  <svg class="hero-cut" viewBox="0 0 1200 100" preserveAspectRatio="none" aria-hidden="true">
    <polygon points="0,92 605,0 1200,92 1200,100 0,100" fill="#ffffff"/>
  </svg>
  <h1 class="hero-title">Corran Industries</h1>
  <p class="hero-lead">A single point of Contact for all<br>Your Procurement Needs</p>
  <div class="hero-arrows">
    <svg viewBox="0 0 28 28" aria-hidden="true"><circle cx="14" cy="14" r="13" fill="rgba(0,0,0,.45)"/><path d="M16 9 L11 14 L16 19" fill="none" stroke="#fff" stroke-width="2"/></svg>
    <svg viewBox="0 0 28 28" aria-hidden="true"><circle cx="14" cy="14" r="13" fill="rgba(0,0,0,.45)"/><path d="M12 9 L17 14 L12 19" fill="none" stroke="#fff" stroke-width="2"/></svg>
  </div>

  <div class="about-frame"></div>
  <section class="about-card">
    <div class="about-photo" role="img" aria-label="Hands at a laptop with a glowing circuit diagram overlay"></div>
    <div class="about-body">
      <h2 class="about-title">About us</h2>
      <p class="about-text">We are committed to consistently exceeding customer expectations by providing products, services and sourcing solutions of the highest standard of quality. With our streamlined processes our method is efficient, provides value and ensures on time delivery. Our success is based on continuously improving the efficiencies and effectiveness of our products, processes, and quality management systems.</p>
      <span class="pill-button">Read More</span>
    </div>
  </section>

  <section class="services">
    <svg class="services-bg" viewBox="0 0 1200 600" preserveAspectRatio="none" aria-hidden="true">
      <polygon points="0,0 596,86 596,600 0,600" fill="#e8501c"/>
      <polygon points="596,86 1200,0 1200,600 596,600" fill="#1d1e21"/>
      <line x1="596" y1="86" x2="596" y2="600" stroke="#6a6a6a" stroke-width="1"/>
    </svg>
    <div class="service service-machining">
      <div class="service-head">
        <h3 class="service-title">MACHINING</h3>
        <div class="service-icons" role="img" aria-label="Line icons of a blueprint, a robotic arm and a machine"></div>
      </div>
      <p class="service-text">Corran Industries brings their machining knowledge to the table every day working closely with our customers to put value into each part we produce. Working as a strategic partner, Corran Industries is able to deliver precision machined components with the highest quality, on time, and at the most cost effective price.</p>
      <ul class="service-list">
        <li><svg viewBox="0 0 18 18"><circle cx="9" cy="9" r="9" fill="#fff"/><path d="M10.5 5 L6.5 9 L10.5 13" fill="none" stroke="#e8501c" stroke-width="2.2"/></svg>Multiple Axis Equipment</li>
        <li><svg viewBox="0 0 18 18"><circle cx="9" cy="9" r="9" fill="#fff"/><path d="M10.5 5 L6.5 9 L10.5 13" fill="none" stroke="#e8501c" stroke-width="2.2"/></svg>Prototypes to Production Runs</li>
        <li><svg viewBox="0 0 18 18"><circle cx="9" cy="9" r="9" fill="#fff"/><path d="M10.5 5 L6.5 9 L10.5 13" fill="none" stroke="#e8501c" stroke-width="2.2"/></svg>Assembiles</li>
        <li><svg viewBox="0 0 18 18"><circle cx="9" cy="9" r="9" fill="#fff"/><path d="M10.5 5 L6.5 9 L10.5 13" fill="none" stroke="#e8501c" stroke-width="2.2"/></svg>Custom Built Fixtures/tooling</li>
      </ul>
    </div>
    <div class="service service-sourcing">
      <div class="service-head">
        <h3 class="service-title">SOURCING</h3>
        <div class="service-icons" role="img" aria-label="Line icons of a map, a checklist and a delivery truck"></div>
      </div>
      <p class="service-text">Over the years we identified the need to provide one stop services to purchasing departments. We have built an extensive network of hard to find products, machining specialists and leveraging open machine time to provide the most economical alternatives to our customers. We have developed a specialized method to supply our customers with the benefits they desire.</p>
      <ul class="service-list">
        <li><svg viewBox="0 0 18 18"><circle cx="9" cy="9" r="9" fill="#fff"/><path d="M10.5 5 L6.5 9 L10.5 13" fill="none" stroke="#1d1e21" stroke-width="2.2"/></svg>Vetting</li>
        <li><svg viewBox="0 0 18 18"><circle cx="9" cy="9" r="9" fill="#fff"/><path d="M10.5 5 L6.5 9 L10.5 13" fill="none" stroke="#1d1e21" stroke-width="2.2"/></svg>Quality</li>
        <li><svg viewBox="0 0 18 18"><circle cx="9" cy="9" r="9" fill="#fff"/><path d="M10.5 5 L6.5 9 L10.5 13" fill="none" stroke="#1d1e21" stroke-width="2.2"/></svg>Process</li>
        <li><svg viewBox="0 0 18 18"><circle cx="9" cy="9" r="9" fill="#fff"/><path d="M10.5 5 L6.5 9 L10.5 13" fill="none" stroke="#1d1e21" stroke-width="2.2"/></svg>Benefits</li>
      </ul>
    </div>
  </section>

  <section class="contact">
    <h2 class="contact-title">CONTACT US</h2>
    <p class="contact-lead">Today with your machining or sourcing needs!</p>
    <span class="pill-button">Get in touch</span>
  </section>

  <footer class="site-footer">© 2019 Company Name&nbsp; All right reserved</footer>
</body>
</html>
```